KV HOLDING Business Cards

I need business cards for "KV Holding group LLC" doublesided... logo on the back (also include logo on front)
logo attached to project... i have jpg up..
Company Info:
827 North Cadwell Avenue, Suite 4B
Lakeview Falls, Illinois 60917
facsimile 312-481-2075 (list fax, address, website on all cards.)
www.kvholdinggroup.example
Three different people on cards:
Darnell P. Okafor, CPA MST
Principal
ofc 312-481-3900
mobile 312-204-7751
darnellpokafor@kvholdinggroup.example
Hollis T. Brennecke, CPA MST
Principal
hollistbrennecke@kvholdinggroup.example
mobile 708-539-1184
ofc 312-481-3900
Conrad M Pavlik
Principal
ofc 312-481-3900
no mobile
conradmpavlik@kvholdinggroup.example
I have multiple projects listed.. see below:
Business cards for amber gate ventures llc
letterhead
envelopes
Business cards for KV Holding LLC
letterhead
envelopes
Target Market(s)
rich people
Industry/Entity Type
Business
Look and feel
Each slider illustrates characteristics of the customer's brand and the style your logo design should communicate.

```html
<!DOCTYPE html>
<html lang="en">
<head>
<meta charset="utf-8">
<title>KV Holding Group LLC — Business Cards</title>
<link rel="stylesheet" href="https://fonts.googleapis.com/css2?family=Exo+2:ital,wght@0,400;0,500;0,600;1,400;1,600&display=swap">
<style>
  :root {
    --page-bg: #d9dadc;
    --navy: #0d3f80;
    --royal-top: #0a5ccc;
    --royal-bottom: #073f92;
    --ink: #1b1f2a;
    --rule: #8a8f98;
    --paper: #ffffff;
  }
  * { box-sizing: border-box; margin: 0; padding: 0; }
  html, body { width: 1200px; height: 1012px; overflow: hidden; }
  body {
    background: var(--page-bg);
    font-family: "Exo 2", "Segoe UI", sans-serif;
    color: var(--ink);
    position: relative;
  }
  .card {
    position: absolute;
    left: 200px;
    width: 800px;
    height: 457px;
    box-shadow: 0 6px 18px rgba(0,0,0,0.18);
    overflow: hidden;
  }
  /* Back */
  .card-back {
    top: 36px;
    background: linear-gradient(180deg, var(--royal-top) 0%, var(--royal-bottom) 100%);
    display: flex;
    align-items: center;
    justify-content: center;
  }
  .brand-back {
    display: flex;
    align-items: center;
    gap: 16px;
    color: var(--paper);
    font-size: 40px;
    font-weight: 500;
  }
  .brand-back .brand-mark { width: 20px; height: 20px; background: var(--paper); }
  /* Front */
  .card-front { top: 519px; background: var(--paper); }
  .brand-front {
    position: absolute; left: 42px; top: 32px;
    display: flex; align-items: center; gap: 10px;
    color: var(--navy);
    font-size: 21px;
    font-weight: 500;
  }
  .brand-front .brand-mark { width: 12px; height: 12px; background: var(--navy); }
  .brand-rule {
    position: absolute; left: 42px; top: 72px; width: 230px; height: 1px; background: var(--rule);
  }
  .company-address {
    position: absolute; right: 34px; top: 28px;
    text-align: right; color: var(--navy);
    font-size: 14px; font-weight: 600; line-height: 1.3; font-style: normal;
  }
  .contact-heading {
    position: absolute; left: 350px; top: 158px; width: 420px;
    display: flex; align-items: center; gap: 12px;
    color: var(--navy); font-size: 21px; font-weight: 600;
  }
  .contact-heading .line { flex: 1; height: 1px; background: var(--rule); }
  .contact-heading .tail { position: absolute; right: 0; top: 30px; width: 120px; height: 1px; background: var(--rule); }
  .person { position: absolute; font-size: 13px; line-height: 1.32; }
  .person .row { display: flex; align-items: center; gap: 7px; }
  .person .name { font-weight: 600; }
  .person .indent { padding-left: 18px; font-style: italic; }
  .icon { width: 11px; height: 11px; fill: var(--navy); flex: none; }
  .person-hollis { left: 42px; top: 92px; }
  .person-darnell { left: 42px; top: 204px; }
  .person-conrad { left: 420px; top: 204px; }
  .footer-band { position: absolute; left: 0; top: 0; width: 800px; height: 457px; }
  .band-fill { fill: var(--navy); }
  .website {
    position: absolute; left: 30px; top: 416px;
    color: var(--paper); font-size: 15px; font-weight: 600; font-style: italic;
  }
</style>
</head>
<body>
<svg width="0" height="0" style="position:absolute" aria-hidden="true">
  <symbol id="i-person" viewBox="0 0 12 12"><circle cx="6" cy="3.5" r="2.8"/><path d="M0.5 12c0-3.5 2.5-5 5.5-5s5.5 1.5 5.5 5z"/></symbol>
  <symbol id="i-office" viewBox="0 0 12 12"><rect x="1" y="3" width="10" height="8" rx="1"/><rect x="3" y="1" width="6" height="3" rx="0.5"/></symbol>
  <symbol id="i-phone" viewBox="0 0 12 12"><path d="M2.5 0.8l2 2.2-1 1.5c0.8 1.6 2 2.8 3.6 3.6l1.5-1 2.2 2-1.2 2C5 11 1 7 0.8 2z"/></symbol>
  <symbol id="i-mail" viewBox="0 0 12 12"><rect x="0.5" y="2" width="11" height="8" rx="0.8"/><path d="M0.8 2.4l5.2 4 5.2-4" fill="none" stroke="#fff" stroke-width="1"/></symbol>
</svg>

<section class="card card-back" aria-label="Card back">
  <div class="brand-back"><span class="brand-mark"></span><span>KV Holding group LLC</span></div>
</section>

<section class="card card-front" aria-label="Card front">
  <svg class="footer-band" viewBox="0 0 800 457" aria-hidden="true">
    <polygon class="band-fill" points="0,395 318,395 424,300 800,300 800,457 0,457"/>
  </svg>

  <div class="brand-front"><span class="brand-mark"></span><span>KV Holding group LLC</span></div>
  <div class="brand-rule"></div>

  <address class="company-address">
    827 North Cadwell Avenue, Suite 4B<br>
    Lakeview Falls, Illinois 60917<br>
    facsimile 312-481-2075
  </address>

  <div class="contact-heading"><span class="line"></span><span>Contact Details</span><span class="tail"></span></div>

  <div class="person person-hollis">
    <div class="row name"><svg class="icon"><use href="#i-person"/></svg>Hollis T. Brennecke, CPA MST</div>
    <div class="indent">Principal</div>
    <div class="row"><svg class="icon"><use href="#i-office"/></svg>ofc 312-481-3900</div>
    <div class="row"><svg class="icon"><use href="#i-phone"/></svg>mobile 708-539-1184</div>
    <div class="row"><svg class="icon"><use href="#i-mail"/></svg>hollistbrennecke@kvholdinggroup.example</div>
  </div>

  <div class="person person-darnell">
    <div class="row name"><svg class="icon"><use href="#i-person"/></svg>Darnell P. Okafor, CPA MST</div>
    <div class="indent">Principal</div>
    <div class="row"><svg class="icon"><use href="#i-office"/></svg>ofc 312-481-3900</div>
    <div class="row"><svg class="icon"><use href="#i-phone"/></svg>mobile 312-204-7751</div>
    <div class="row"><svg class="icon"><use href="#i-mail"/></svg>darnellpokafor@kvholdinggroup.example</div>
  </div>

  <div class="person person-conrad">
    <div class="row name"><svg class="icon"><use href="#i-person"/></svg>Conrad M Pavlik</div>
    <div class="indent">Principal</div>
    <div class="row"><svg class="icon"><use href="#i-office"/></svg>ofc 312-481-3900</div>
    <div class="row"><svg class="icon"><use href="#i-mail"/></svg>conradmpavlik@kvholdinggroup.example</div>
  </div>

  <div class="website">Visit our Website : www.kvholdinggroup.example</div>
</section>
</body>
</html>
```